New Webpage for High Class Expert Witness Services Company

We are looking for a minimalist design for a webpage that just has our logo and an entry form offer to connect with one of our Liaisons.
The entry form should just ask for Name, Email, Contact Info and Description of Project.

Company Name is: The Marlowe Crest Advisory Services

Number of Pages Required

1 page

```html
<!DOCTYPE html>
<html lang="en">
<head>
<meta charset="utf-8">
<title>The Marlowe Crest Advisory Services</title>
<link rel="stylesheet" href="https://fonts.googleapis.com/css2?family=Cinzel:wght@400;500&family=Montserrat:wght@300;400;600&display=swap">
<style>
  :root {
    --bg-deep: #0b0a09;
    --bg-mid: #171512;
    --glow: rgba(150, 112, 52, 0.42);
    --gold: #b48a3c;
    --gold-button: #6e5526;
    --text-light: #e9e6e0;
    --text-muted: #a9a59d;
    --field: #e4e2de;
    --card-edge: rgba(255, 255, 255, 0.14);
    --card-fill: rgba(70, 60, 44, 0.45);
  }
  * { box-sizing: border-box; margin: 0; padding: 0; }
  html, body { width: 1200px; height: 840px; overflow: hidden; }
  body {
    font-family: "Montserrat", sans-serif;
    color: var(--text-light);
    background:
      radial-gradient(ellipse 420px 460px at 900px 420px, var(--glow), transparent 70%),
      linear-gradient(90deg, var(--bg-deep) 0%, var(--bg-mid) 55%, #2a2319 100%);
    position: relative;
  }
  .brand {
    position: absolute; left: 44px; top: 196px;
    display: flex; align-items: center; gap: 12px;
  }
  .brand-mark { width: 22px; height: 22px; background: var(--text-light); }
  .brand-text { display: flex; flex-direction: column; gap: 3px; }
  .brand-name {
    font-family: "Cinzel", serif; font-weight: 500; font-size: 18px;
    letter-spacing: 0.04em; color: var(--text-light); line-height: 1.1;
  }
  .brand-tagline {
    font-size: 7px; letter-spacing: 0.22em; text-transform: uppercase;
    color: var(--text-muted);
  }
  .hero { position: absolute; left: 44px; top: 336px; width: 560px; }
  .hero-title {
    font-family: "Cinzel", serif; font-weight: 400; font-size: 38px;
    line-height: 1.25; letter-spacing: 0.03em; color: var(--text-light);
  }
  .hero-sub {
    margin-top: 18px; font-weight: 300; font-size: 18px;
    letter-spacing: 0.03em; color: var(--text-muted);
  }
  .hero-assurances {
    margin-top: 22px; display: flex; gap: 22px;
    font-weight: 300; font-size: 15px; color: var(--text-muted);
  }
  .hero-assurances strong { color: var(--gold); font-weight: 600; }
  .consult-card {
    position: absolute; left: 714px; top: 200px; width: 357px; height: 422px;
    border-radius: 16px; border: 1px solid var(--card-edge);
    background: var(--card-fill); padding: 20px 42px 0;
  }
  .consult-title {
    text-align: center; font-weight: 300; font-size: 20px; color: var(--text-muted);
    margin-bottom: 22px;
  }
  .consult-title strong { font-weight: 600; color: var(--text-light); }
  .field { display: block; margin-bottom: 10px; }
  .field span { display: block; font-size: 9px; color: var(--text-light); margin-bottom: 3px; }
  .field input, .field textarea {
    width: 100%; height: 34px; border: none; border-radius: 2px;
    background: var(--field); font-family: inherit;
  }
  .field textarea { height: 88px; resize: none; }
  .consult-submit {
    margin-top: 6px; width: 100%; height: 34px; border: none;
    background: var(--gold-button); color: var(--text-light);
    font-family: inherit; font-size: 10px; letter-spacing: 0.02em;
  }
</style>
</head>
<body>
  <header class="brand">
    <div class="brand-mark"></div>
    <div class="brand-text">
      <div class="brand-name">The Marlowe Crest Advisory Services</div>
      <div class="brand-tagline">Discreet expert counsel integration</div>
    </div>
  </header>

  <section class="hero">
    <h1 class="hero-title">Strategic Defense for<br>High Stakes Matters</h1>
    <p class="hero-sub">Expert witness integration &amp; legal defense support</p>
    <p class="hero-assurances">
      <span><strong>100%</strong> Confidential</span>
      <span><strong>24 hr</strong> Response guarantee</span>
    </p>
  </section>

  <form class="consult-card">
    <h2 class="consult-title">Tell us about Your <strong>Matter</strong></h2>
    <label class="field"><span>Full Name</span><input type="text"></label>
    <label class="field"><span>Email</span><input type="email"></label>
    <label class="field"><span>Contact Number</span><input type="tel"></label>
    <label class="field"><span>Description of Project</span><textarea></textarea></label>
    <button class="consult-submit" type="button">Request Consultation</button>
  </form>
</body>
</html>
```